U.S. Popcorn company needs business cards

We are a popcorn company that manufactures popcorn and sells it to grocery stores worldwide. Our theme is "Americana" and our logo is U.S. route 66 which is the most famous highway in the U.S.

We would like the design to be simple and to use both sides. On the back side we would like to see just the logo and website. The front would be normal details

Target Market(s)

Wholesalers, grocers and distributors

Industry/Entity Type

Manufacture

Contact Information for Business Card

Business name: Prairie Lantern Popcorn
Phone: +1 555 308 4726
Email: Dale@prairielanternpopcorn.com
website: www.prairielanternpopcorn.com
Tag Line: "Fresh from the prairie"
Name: Dale Whitcombe
Title: Founder/President

Requirements
Must have
• Either this design should be fun or clean and simple. I will let you show me your thougths.
Nice to have
• Anything that ties in the real Hwy Route 66.
• Colors might need to be red, white and blue incorporated.
Should not have
• Not be too busy.

```html
<!DOCTYPE html>
<html lang="en">
<head>
<meta charset="utf-8">
<title>Prairie Lantern Popcorn — Business Cards</title>
<link href="https://fonts.googleapis.com/css2?family=Lato:wght@400;700;900&display=swap" rel="stylesheet">
<style>
  :root {
    --navy: #1f3a8c;
    --navy-deep: #172c6e;
    --navy-light: #2b4aa6;
    --red: #e2222f;
    --paper: #f7f7f6;
    --slate: #3b4f86;
    --rule: #7f8bb3;
    --backdrop: #e6e3dc;
    --white: #ffffff;
  }
  * { box-sizing: border-box; margin: 0; padding: 0; }
  html, body {
    width: 1200px; height: 780px; overflow: hidden;
    background: var(--backdrop);
    font-family: "Lato", "Helvetica Neue", Arial, sans-serif;
  }
  .stage {
    position: relative; width: 1200px; height: 780px;
    display: flex; justify-content: center; align-items: center; gap: 90px;
  }
  .card {
    position: relative; width: 340px; height: 580px;
    border-radius: 22px; overflow: hidden;
    box-shadow: 0 10px 28px rgba(0,0,0,.18);
  }

  /* Front */
  .card--front { background: var(--paper); }
  .brand {
    position: absolute; top: 62px; left: 0; right: 0;
    display: flex; flex-direction: column; align-items: center; gap: 14px;
  }
  .brand__dot {
    width: 58px; height: 58px; border-radius: 50%; background: var(--red);
  }
  .brand__name {
    font-weight: 900; font-size: 27px; color: var(--navy);
    text-align: center; line-height: 1.1; width: 240px;
  }
  .tagline {
    position: absolute; top: 222px; left: 0; right: 0; text-align: center;
    color: var(--slate); font-size: 18px; letter-spacing: .3px; white-space: nowrap;
  }
  .person { position: absolute; top: 272px; left: 0; right: 0; text-align: center; }
  .person__name { color: var(--navy); font-size: 31px; font-weight: 400; line-height: 1.1; }
  .person__title { color: var(--red); font-size: 19px; margin-top: 2px; }
  .divider {
    position: absolute; top: 350px; left: 40px; right: 40px;
    height: 1px; background: var(--rule);
  }
  .contact { position: absolute; top: 364px; left: 0; right: 0; text-align: center; }
  .contact__label { color: var(--red); font-weight: 700; font-size: 14px; }
  .contact__value { color: var(--navy); font-size: 18px; margin-bottom: 8px; white-space: nowrap; }
  .contact__value--email { font-size: 17px; }
  .band {
    position: absolute; left: 0; right: 0; bottom: 0; height: 92px;
    background: var(--navy);
    display: flex; align-items: center; justify-content: center;
  }
  .band::before {
    content: ""; position: absolute; left: 0; right: 0; top: -12px; height: 12px;
    background: linear-gradient(var(--paper) 0 3px, var(--red) 3px 5px, var(--paper) 5px 12px);
  }
  .band__web { color: var(--white); font-size: 18px; letter-spacing: .3px; white-space: nowrap; }

  /* Back */
  .card--back {
    background: radial-gradient(ellipse at 45% 45%, var(--navy-light) 0%, var(--navy) 55%, var(--navy-deep) 100%);
  }
  .back__text {
    position: absolute; top: 50%; left: 50%;
    width: 540px; transform: translate(-50%, -50%) rotate(90deg);
    text-align: center; color: var(--white);
  }
  .back__name {
    font-weight: 900; font-size: 30px; letter-spacing: 1px; text-transform: uppercase;
    white-space: nowrap;
  }
  .back__web { font-size: 17px; margin-top: 6px; letter-spacing: .3px; white-space: nowrap; }
</style>
</head>
<body>
  <main class="stage">
    <section class="card card--front" aria-label="Business card front">
      <div class="brand">
        <span class="brand__dot" aria-hidden="true"></span>
        <span class="brand__name">Prairie Lantern Popcorn</span>
      </div>
      <p class="tagline">Fresh from the prairie</p>
      <div class="person">
        <p class="person__name">Dale Whitcombe</p>
        <p class="person__title">Founder/President</p>
      </div>
      <div class="divider"></div>
      <div class="contact">
        <p class="contact__label">Phone</p>
        <p class="contact__value">+1 555 308 4726</p>
        <p class="contact__label">Email</p>
        <p class="contact__value contact__value--email">Dale@prairielanternpopcorn.com</p>
      </div>
      <div class="band">
        <span class="band__web">www.prairielanternpopcorn.com</span>
      </div>
    </section>

    <section class="card card--back" aria-label="Business card back">
      <div class="back__text">
        <p class="back__name">Prairie Lantern Popcorn</p>
        <p class="back__web">www.prairielanternpopcorn.com</p>
      </div>
    </section>
  </main>
</body>
</html>
```